Meridale Bed Company Needs Business Card

Looking for a very nice looking business card. Creative but not extravagant. We sell beds and pillows across the U.S. and need something professional but catchy. I have attached the logo.

Name : Devin Holt
Title : President
Phone : (800) 471-2960
Email: sleep@quilmora.com
Website: www.quilmora.com

Can be single-sided or double-sided
horizontal or vertical

Can use Blues/Greys

Target Market(s)

Mass Market

Industry/Entity Type

Retail

Contact Information for Business Card

Name : Devin Holt
Title : President
Phone : (800) 471-2960
Email: sleep@quilmora.com
Website: www.quilmora.com

Requirements
Must have
• Clean, Modern, Smooth
• Can use Blues/Greys
• On the other side without the information - have something simple like www.quilmora.com or our logo
Nice to have
• Surprise me
Should not have
• Nothing crazy, nothing cluttered

```html
<!DOCTYPE html>
<html lang="en">
<head>
<meta charset="utf-8">
<title>Meridale Bed Company – Business Card</title>
<link href="https://fonts.googleapis.com/css2?family=Nunito:wght@300;400;600&display=swap" rel="stylesheet">
<style>
  :root {
    --backdrop: #3b3b3d;
    --card-blue: #1f96ca;
    --card-blue-light: #27a2d6;
    --card-white: #f7f7f7;
    --card-grey: #e6e6e6;
    --brand-blue: #2aa3d7;
    --text-grey: #555659;
    --text-dark: #46474a;
    --white: #ffffff;
  }
  * { margin: 0; padding: 0; box-sizing: border-box; }
  html, body {
    width: 1200px; height: 787px; overflow: hidden;
    background: var(--backdrop);
    font-family: "Nunito", sans-serif;
  }
  .canvas { position: relative; width: 1200px; height: 787px; }
  .card {
    position: absolute; top: 239px;
    width: 534px; height: 299px;
    border-radius: 18px;
    overflow: hidden;
  }
  .card--back {
    left: 46px;
    background: linear-gradient(120deg, var(--card-blue) 0%, var(--card-blue-light) 100%);
  }
  .card--back .web {
    position: absolute; right: 44px; top: 40px;
    color: var(--white); font-size: 14.5px; font-weight: 600;
    letter-spacing: 1px;
  }
  .card--front {
    left: 630px;
    background: linear-gradient(115deg, var(--card-white) 0%, var(--card-grey) 100%);
  }
  .brand {
    position: absolute; left: 26px; top: 16px;
    color: var(--brand-blue); font-size: 56px; font-weight: 300;
    letter-spacing: 1px;
  }
  .person { position: absolute; left: 27px; top: 189px; }
  .person .name { color: var(--text-grey); font-size: 21px; font-weight: 400; letter-spacing: .5px; }
  .person .title { color: var(--brand-blue); font-size: 15px; font-weight: 600; margin-top: 3px; letter-spacing: .3px; }
  .icons {
    position: absolute; right: 26px; top: 195px;
    display: flex; gap: 8px;
  }
  .icon {
    width: 19px; height: 19px; border-radius: 50%;
    background: var(--brand-blue);
    display: flex; align-items: center; justify-content: center;
  }
  .contact {
    position: absolute; right: 26px; top: 225px;
    text-align: right; font-size: 14.5px; line-height: 16.5px; font-weight: 600;
    color: var(--text-dark);
  }
  .contact .site { color: var(--brand-blue); }
</style>
</head>
<body>
<main class="canvas">
  <section class="card card--back" aria-label="Card back">
    <p class="web">www.quilmora.com</p>
  </section>

  <section class="card card--front" aria-label="Card front">
    <p class="brand">quilmora</p>
    <div class="person">
      <p class="name">Devin Holt</p>
      <p class="title">President</p>
    </div>
    <div class="icons">
      <span class="icon" aria-label="Phone">
        <svg width="11" height="11" viewBox="0 0 12 12" fill="none" stroke="#fff" stroke-width="1.3">
          <path d="M1.5 4.5 Q6 1 10.5 4.5 L9.5 6 L7.8 5.2 V4.2 H4.2 V5.2 L2.5 6 Z" fill="#fff"/>
          <rect x="3" y="6.5" width="6" height="3.5" rx=".6" fill="#fff" stroke="none"/>
        </svg>
      </span>
      <span class="icon" aria-label="Email">
        <svg width="11" height="11" viewBox="0 0 12 12" fill="none" stroke="#fff" stroke-width="1.1">
          <rect x="1.5" y="3" width="9" height="6.2" rx=".5"/>
          <path d="M1.7 3.3 L6 6.6 L10.3 3.3 M1.7 9 L4.6 5.6 M10.3 9 L7.4 5.6"/>
        </svg>
      </span>
      <span class="icon" aria-label="Website">
        <svg width="11" height="11" viewBox="0 0 12 12" fill="none" stroke="#fff" stroke-width="1">
          <circle cx="6" cy="6" r="4.6"/>
          <ellipse cx="6" cy="6" rx="2" ry="4.6"/>
          <path d="M1.4 6 H10.6 M2.2 3.6 H9.8 M2.2 8.4 H9.8"/>
        </svg>
      </span>
    </div>
    <div class="contact">
      <p>(800) 471-2960</p>
      <p>sleep@quilmora.com</p>
      <p class="site">www.quilmora.com</p>
    </div>
  </section>
</main>
</body>
</html>
```